BFCM Creatives Theme

We are looking for an initial design for our BFCM campaign this year to set the theme for all other creatives for BFCM. We are an ecommerce brand selling Merino wool baby clothing. Our flagship product is the Marlow Toddler Hush Pod (see images).

We are starting with the request for an instagram post, announcing the sale (details below). This post should be 1080x1350 but also look appealing in the square grid. I've attached a basic brand card showing color palette, fonts, and logos. I will also attach some image options. We are looking for your creativity to shine while aligning with our branding and connecting with the customer. If you have a specific idea and are looking for a specific image please contact us.

Sale Details:
- 20% Off Sitewide
- 11.28.24 - 12.02.24
- Excluding giftcards and imperfects. No rainchecks.

```html
<!DOCTYPE html>
<html lang="en">
<head>
<meta charset="utf-8">
<title>Fernlamb – 20% Off Sitewide</title>
<link href="https://fonts.googleapis.com/css2?family=Poppins:wght@500;600;700;800&family=Caveat:wght@500&display=swap" rel="stylesheet">
<style>
  :root {
    --sage: #c5d1c1;
    --charcoal: #333438;
    --cream: #f1efec;
    --white: #ffffff;
    --stage: #5a5a5a;
    --photo-light: #e9ece4;
    --photo-mid: #b9c8a8;
    --photo-deep: #7f9a6e;
  }
  html, body {
    margin: 0;
    padding: 0;
    width: 1200px;
    height: 1197px;
    overflow: hidden;
    background: var(--stage);
  }
  .post {
    position: absolute;
    left: 135px;
    top: 18px;
    width: 930px;
    height: 1162.5px;
    display: block;
  }
  .brand-name {
    font-family: "Poppins", sans-serif;
    font-weight: 600;
    fill: var(--charcoal);
  }
  .offer-big {
    font-family: "Poppins", sans-serif;
    font-weight: 800;
    fill: var(--cream);
  }
  .offer-sub {
    font-family: "Poppins", sans-serif;
    font-weight: 700;
    fill: var(--cream);
  }
  .sale-dates {
    font-family: "Poppins", sans-serif;
    font-weight: 600;
    fill: var(--cream);
  }
  .terms {
    font-family: "Caveat", cursive;
    font-weight: 500;
    fill: var(--charcoal);
  }
</style>
</head>
<body>
<svg class="post" viewBox="0 0 1080 1350" xmlns="http://www.w3.org/2000/svg">
  <defs>
    <clipPath id="post-bounds">
      <rect x="0" y="0" width="1080" height="1350"/>
    </clipPath>
    <linearGradient id="photo-tones" x1="0" y1="0" x2="0.6" y2="1">
      <stop offset="0" stop-color="var(--photo-light)"/>
      <stop offset="0.55" stop-color="var(--photo-mid)"/>
      <stop offset="1" stop-color="var(--photo-deep)"/>
    </linearGradient>
  </defs>

  <g clip-path="url(#post-bounds)">
    <rect class="backdrop" x="0" y="0" width="1080" height="1350" fill="var(--sage)"/>

    <!-- hero image frame -->
    <circle class="hero-arc" cx="760" cy="230" r="590" fill="var(--charcoal)"/>
    <circle class="hero-photo" cx="740" cy="170" r="600" fill="url(#photo-tones)"
            role="img" aria-label="Smiling baby standing in a white crib wearing a sage green wool sleep sack"/>

    <!-- brand tag -->
    <rect class="brand-tag" x="0" y="64" width="457" height="105" fill="var(--white)"/>
    <circle class="brand-dot" cx="70" cy="116.5" r="30" fill="var(--charcoal)"/>
    <text class="brand-name" x="122" y="141" font-size="66">Fernlamb</text>

    <!-- offer badge -->
    <circle class="offer-ring" cx="262" cy="1212" r="432" fill="var(--cream)"/>
    <circle class="offer-disc" cx="240" cy="1200" r="420" fill="var(--charcoal)"/>
    <text class="offer-big" x="52" y="1029" font-size="214" letter-spacing="-4">20%</text>
    <text class="offer-big" x="52" y="1207" font-size="214" letter-spacing="-2">OFF</text>
    <text class="offer-sub" x="54" y="1311" font-size="104" letter-spacing="-1">Sitewide</text>

    <!-- calendar icon -->
    <g class="calendar-icon" fill="none" stroke="var(--charcoal)" stroke-width="5">
      <rect x="848" y="886" width="62" height="56" rx="7"/>
      <line x1="863" y1="876" x2="863" y2="893" stroke-linecap="round"/>
      <line x1="895" y1="876" x2="895" y2="893" stroke-linecap="round"/>
    </g>
    <g class="calendar-grid" fill="var(--charcoal)">
      <rect x="848" y="886" width="62" height="14" rx="6"/>
      <rect x="855" y="906" width="9" height="7"/><rect x="868" y="906" width="9" height="7"/>
      <rect x="881" y="906" width="9" height="7"/><rect x="894" y="906" width="9" height="7"/>
      <rect x="855" y="917" width="9" height="7"/><rect x="868" y="917" width="9" height="7"/>
      <rect x="881" y="917" width="9" height="7"/><rect x="894" y="917" width="9" height="7"/>
      <rect x="855" y="928" width="9" height="7"/><rect x="868" y="928" width="9" height="7"/>
      <rect x="881" y="928" width="9" height="7"/>
    </g>

    <!-- sale dates -->
    <rect class="date-pill" x="658" y="960" width="460" height="55" rx="27.5" fill="var(--charcoal)"/>
    <text class="sale-dates" x="869" y="1003" font-size="42" text-anchor="middle">11.28.24 - 12.02.24</text>

    <!-- terms -->
    <circle class="term-bullet" cx="723" cy="1099" r="7" fill="var(--charcoal)"/>
    <text class="terms" x="755" y="1110" font-size="46">Excluding giftcards</text>
    <text class="terms" x="755" y="1162" font-size="46">and imperfects</text>
    <circle class="term-bullet" cx="723" cy="1207" r="7" fill="var(--charcoal)"/>
    <text class="terms" x="755" y="1218" font-size="46">No rainchecks</text>
  </g>
</svg>
</body>
</html>
```